Professional Photography Business cards

I need business cards that include my logo which I have uploaded. I run a photography business. I am open to ideas but I would like one side to have my logo and the other side to have my contact info. I don't have a website made but I do own a website domain. I have uploaded 2 different logo color schemes. My business colors are Blue, black , and white.

Business Name
Business Phone Number
Business Email
Business Website address
Instagram

Industry/Entity Type

Professional Photography

Contact Information for Business Card

Phone Number: 916-384-7702 email: info@tlane-studio.example Instagram: @t.lanestudio website doman- www.tlane-studio.example

Requirements
Must have
• I like the idea of a business card with a full black background front and back of card. My colors must include royal blue, black, and white

```html
<!DOCTYPE html>
<html lang="en">
<head>
<meta charset="utf-8">
<title>T. Lane Studio – Business Cards</title>
<link rel="stylesheet" href="https://fonts.googleapis.com/css2?family=Montserrat:wght@500;700&family=Roboto:wght@400;500&display=swap">
<style>
  :root {
    --backdrop: #1c1c1e;
    --royal-light: #5661b9;
    --royal: #3a43a6;
    --royal-deep: #232a8e;
    --ink-white: #ffffff;
    --soft-white: rgba(255,255,255,0.88);
  }
  * { box-sizing: border-box; margin: 0; padding: 0; }
  html, body {
    width: 1200px; height: 929px; overflow: hidden;
    background: var(--backdrop);
  }
  .sheet {
    position: relative; width: 1200px; height: 929px;
    display: flex; flex-direction: column; align-items: center; justify-content: center;
    gap: 36px;
  }
  .card {
    position: relative; width: 700px; height: 400px; border-radius: 22px;
    background: radial-gradient(ellipse at 55% 40%, var(--royal-light) 0%, var(--royal) 45%, var(--royal-deep) 100%);
    color: var(--ink-white);
    overflow: hidden;
  }
  .brand {
    display: flex; align-items: center; gap: 14px;
    font-family: "Montserrat", sans-serif; font-weight: 500;
    color: var(--ink-white); letter-spacing: 0.04em;
  }
  .brand-dot {
    border: 3px solid var(--ink-white); border-radius: 50%;
    flex: none;
  }
  .card-front .brand {
    position: absolute; left: 50%; top: 50%; transform: translate(-50%, -50%);
    font-size: 40px;
  }
  .card-front .brand-dot { width: 58px; height: 58px; }

  .card-back .brand {
    position: absolute; left: 70px; top: 205px;
    font-size: 25px;
  }
  .card-back .brand-dot { width: 38px; height: 38px; border-width: 2.5px; }
  .divider {
    position: absolute; left: 360px; top: 110px; width: 1.5px; height: 190px;
    background: var(--ink-white);
  }
  .contact {
    position: absolute; left: 392px; top: 112px;
  }
  .contact-name {
    font-family: "Montserrat", sans-serif; font-weight: 700; font-size: 30px; line-height: 1.1;
  }
  .contact-title {
    font-family: "Montserrat", sans-serif; font-weight: 500; font-size: 17px;
    margin: 4px 0 22px 2px; color: var(--soft-white);
  }
  .contact-list { list-style: none; font-family: "Roboto", sans-serif; font-size: 15.5px; }
  .contact-list li { display: flex; align-items: center; gap: 8px; margin-bottom: 7px; }
  .contact-list svg { width: 15px; height: 15px; flex: none; fill: var(--ink-white); }
</style>
</head>
<body>
<main class="sheet">
  <section class="card card-front" aria-label="Card front">
    <div class="brand"><span class="brand-dot"></span>T. Lane Studio</div>
  </section>

  <section class="card card-back" aria-label="Card back">
    <div class="brand"><span class="brand-dot"></span>T. Lane Studio</div>
    <div class="divider"></div>
    <div class="contact">
      <h1 class="contact-name">Tessa Lane</h1>
      <p class="contact-title">CPA, CGA</p>
      <ul class="contact-list">
        <li>
          <svg viewBox="0 0 24 24" aria-hidden="true"><path d="M6.6 10.8a15.5 15.5 0 0 0 6.6 6.6l2.2-2.2c.3-.3.7-.4 1-.2 1.1.4 2.3.6 3.6.6.6 0 1 .4 1 1V20c0 .6-.4 1-1 1A17 17 0 0 1 3 4c0-.6.4-1 1-1h3.5c.6 0 1 .4 1 1 0 1.3.2 2.5.6 3.6.1.3 0 .7-.2 1z"/></svg>
          916-384-7702
        </li>
        <li>
          <svg viewBox="0 0 24 24" aria-hidden="true"><path d="M2 5h20v14H2zm2 2v.5l8 5 8-5V7zm0 2.8V17h16V9.8l-8 5z"/></svg>
          info@tlane-studio.example
        </li>
        <li>
          <svg viewBox="0 0 24 24" aria-hidden="true"><path d="M12 2a10 10 0 1 0 0 20 10 10 0 0 0 0-20zm0 2c1 0 2.3 2 2.8 5H9.2C9.7 6 11 4 12 4zM4.3 13a8 8 0 0 1 0-2h2.9a17 17 0 0 0 0 2zm.7 2h2.5c.3 1.5.8 2.8 1.4 3.8A8 8 0 0 1 5 15zm2.5-6H5a8 8 0 0 1 3.9-3.8C8.3 6.2 7.8 7.5 7.5 9zM12 20c-1 0-2.3-2-2.8-5h5.6c-.5 3-1.8 5-2.8 5zm3-7H9a15 15 0 0 1 0-2h6a15 15 0 0 1 0 2zm.1 5.8c.6-1 1.1-2.3 1.4-3.8H19a8 8 0 0 1-3.9 3.8zm1.7-5.8a17 17 0 0 0 0-2h2.9a8 8 0 0 1 0 2zm-.3-4c-.3-1.5-.8-2.8-1.4-3.8A8 8 0 0 1 19 9z"/></svg>
          www.tlane-studio.example
        </li>
        <li>
          <svg viewBox="0 0 24 24" aria-hidden="true"><circle cx="12" cy="12" r="7"/></svg>
          @t.lanestudio
        </li>
      </ul>
    </div>
  </section>
</main>
</body>
</html>
```